High end Natural/Therapeutic, skin care company needs packaging design

We need packaging designs for a line of natural cream deodorants made in Canada. They will be launched in retail spas and health stores this fall.
Our company formulates effective, pretty products bought mainly by women ages 35 to 75. These are top shelf products that deliver exceptional value for their cost.
Our company name is "Willow Brook". We would like Natural Skin Care incorporated as well. The company name should be prominent, legible, duplicatable and recognizable through each product. The product "Deodorant" should be the most prominent. The customer should be able to pick that out easily.
The overall feel of the name and packaging should be feminine, but not frilly. Upscale but not uppity. These are common sense products that make the person feel good about themselves when they see, touch and use them. Each product should have it's own identity, but still have Willow Brook, Natural Skin Care as the recognizable source.
Our packaging for the deodorants is in clear glass 60 mL jars (55mm height X 55mm diameter, label that goes around it is 1" width X maximum of 6.5" long. Circular label on the top of the lid is 1.67". Information on it is Willow Brook Natural Skin care and around that is Reveal your true beauty, naturally.) The jar is in a printed box.
The box is 2.5 inches X 2.5 inches X 2.5 inches. No windows in the box.
Palisade Deodorant cream #1, is Sensitive with Lavender as the main essential oil
fragrance. This package should have the feeling of lightness, airiness and femininity. Palisade Deodorant cream #2 is Extra Strength, with Citrus essential oils as the scent. It should have brighter, bolder colors with a slightly masculine feel.
If you leave room for the directions, ingredients and description, I will fill in the body of the information later. Mainly what I am looking for is the font for the name and product and the artistry and color of your designs.
As well as deodorant, Willow Brook formulates several therapeutic, pain remedies and face serums, toner, and creams. These products use strong, innovative natural ingredients that work for delicate, thin skinned, sensitive skin types. Whenever possible we incorporate Dead Sea minerals from Israel into our products.
Target Market(s)
Women ages 35 to 75
Industry/Entity Type
It Company
Requirements
Must have
- name: WILLOW BROOK Natural Skin Care
Reveal your true beauty, naturally
#1 Palisade Deodorant cream, Sensitive, Lavender
#2 Palisade Deodorant cream Extra Strength, Citrus
Nice to have
- The logo below is what I have been using, but would like to change it. I would like it to look more upscale, bolder, less script. Possibly use Trajan Pro 3 for Willow Brook and a script for Natural Skin care. As well, I do like the font that the Odette example uses.
I have uploaded some examples of packaging that I like. Hope this helps.
Should not have
- Cartoon, childlike characters. Please do not use the existing Willow Brook logo, it is for reference only.

```html
<!DOCTYPE html>
<html lang="en">
<head>
<meta charset="utf-8">
<title>Willow Brook – Palisade Deodorant Cream Labels</title>
<link rel="stylesheet" href="https://fonts.googleapis.com/css2?family=Raleway:wght@300;400;600;700&display=swap">
<style>
  :root {
    --bg-light: #f4f4f6;
    --bg-edge: #d6d5da;
    --paper: #ffffff;
    --lavender: #6e1f6c;
    --lavender-deep: #4a1848;
    --citrus: #7bab24;
    --citrus-deep: #4e7a22;
    --ink: #2a2a2a;
    --ink-soft: #6a6a6a;
    --shadow: rgba(0, 0, 0, 0.12);
  }
  * { box-sizing: border-box; margin: 0; padding: 0; }
  html, body { width: 1200px; height: 900px; overflow: hidden; }
  body {
    background: radial-gradient(ellipse at 50% 50%, var(--bg-light) 0%, var(--bg-light) 45%, var(--bg-edge) 100%);
    font-family: "Raleway", sans-serif;
  }
  .canvas {
    position: relative;
    width: 1200px;
    height: 900px;
    display: flex;
    justify-content: center;
    gap: 80px;
    padding-top: 120px;
  }
  .product { width: 460px; display: flex; flex-direction: column; align-items: center; gap: 50px; }

  /* Lid label */
  .lid-label {
    width: 240px; height: 240px; border-radius: 50%;
    display: flex; flex-direction: column; align-items: center; justify-content: center;
    color: var(--paper); text-align: center;
    box-shadow: 0 4px 14px var(--shadow);
  }
  .product--lavender .lid-label { background: linear-gradient(135deg, var(--lavender), var(--lavender-deep)); }
  .product--citrus .lid-label { background: linear-gradient(135deg, var(--citrus), var(--citrus-deep)); }
  .lid-label__brand { font-size: 20px; font-weight: 600; letter-spacing: 1.5px; }
  .lid-label__line { font-size: 12px; font-weight: 300; margin-top: 4px; letter-spacing: 1px; }
  .lid-label__tagline { font-size: 12px; font-weight: 400; font-style: italic; margin-top: 16px; width: 170px; }

  /* Wrap label */
  .wrap-label {
    position: relative; width: 460px; height: 260px;
    background: var(--paper);
    box-shadow: 0 4px 14px var(--shadow);
  }
  .wrap-label__band { position: absolute; inset: 0; }
  .wrap-label__brand {
    position: absolute; left: 78px; top: 52px; width: 200px; text-align: center;
    color: var(--paper);
  }
  .brand-name { font-size: 20px; font-weight: 600; letter-spacing: 0.5px; }
  .brand-line { font-size: 12px; font-weight: 400; margin-top: 2px; }
  .brand-dot {
    position: absolute; left: 118px; top: 118px; width: 28px; height: 28px;
    border-radius: 50%; background: var(--paper);
  }
  .wrap-label__volume {
    position: absolute; left: 58px; top: 168px; color: var(--paper);
    font-size: 17px; font-weight: 400;
  }
  .wrap-label__volume small { font-size: 11px; }
  .wrap-label__product {
    position: absolute; right: 20px; top: 108px; text-align: right;
  }
  .product-line { font-size: 15px; font-weight: 700; line-height: 1.4; }
  .product--lavender .product-line { color: var(--lavender); }
  .product--citrus .product-line { color: var(--citrus-deep); }
  .product-scent { font-size: 17px; font-weight: 400; color: var(--ink); margin-top: 4px; }
  .product-variant { font-size: 11px; font-weight: 400; color: var(--ink-soft); }
</style>
</head>
<body>
<main class="canvas">

  <section class="product product--lavender">
    <div class="lid-label">
      <p class="lid-label__brand">WILLOW BROOK</p>
      <p class="lid-label__line">Natural Skin Care</p>
      <p class="lid-label__tagline">Reveal your true beauty, naturally</p>
    </div>
    <div class="wrap-label">
      <svg class="wrap-label__band" width="460" height="260" viewBox="0 0 460 260" aria-hidden="true">
        <defs>
          <linearGradient id="band-lavender" x1="0" x2="1" y1="0" y2="0">
            <stop offset="0" stop-color="#6e1f6c"/>
            <stop offset="1" stop-color="#4a1848"/>
          </linearGradient>
        </defs>
        <polygon points="0,30 460,10 115,225 0,210" fill="url(#band-lavender)"/>
      </svg>
      <div class="wrap-label__brand">
        <p class="brand-name">WILLOW BROOK</p>
        <p class="brand-line">natural skin care</p>
      </div>
      <span class="brand-dot"></span>
      <p class="wrap-label__volume">60<small>ml</small></p>
      <div class="wrap-label__product">
        <p class="product-line">Palisade<br>Deodorant cream</p>
        <p class="product-scent">Lavender</p>
        <p class="product-variant">Sensitive</p>
      </div>
    </div>
  </section>

  <section class="product product--citrus">
    <div class="lid-label">
      <p class="lid-label__brand">WILLOW BROOK</p>
      <p class="lid-label__line">Natural Skin Care</p>
      <p class="lid-label__tagline">Reveal your true beauty, naturally</p>
    </div>
    <div class="wrap-label">
      <svg class="wrap-label__band" width="460" height="260" viewBox="0 0 460 260" aria-hidden="true">
        <defs>
          <linearGradient id="band-citrus" x1="0" x2="1" y1="0" y2="0">
            <stop offset="0" stop-color="#7bab24"/>
            <stop offset="1" stop-color="#4e7a22"/>
          </linearGradient>
        </defs>
        <polygon points="0,30 460,10 115,225 0,210" fill="url(#band-citrus)"/>
      </svg>
      <div class="wrap-label__brand">
        <p class="brand-name">WILLOW BROOK</p>
        <p class="brand-line">natural skin care</p>
      </div>
      <span class="brand-dot"></span>
      <p class="wrap-label__volume">60<small>ml</small></p>
      <div class="wrap-label__product">
        <p class="product-line">Palisade<br>Deodorant cream</p>
        <p class="product-scent">Citrus</p>
        <p class="product-variant">Sensitive</p>
      </div>
    </div>
  </section>

</main>
</body>
</html>
```